Stationery Design Project for Nimbora, Chicago

Nimbora, a street parking application which helps car drivers find a street parking spot by offering an ideal path along which to look for parking. This path is calculated by our algorithm based on data (e.g. historical data, baseball games schedule, etc.). Along this path the driver will find a spot and will also save 70% of the search time. Customer we target is reg. between 21 and 45 yo.

We envision something young, fresh, bright and original. Slightly abstract maybe. It should represent the idea and elements of finding street parking in the city, e.g. car(s), parking spot, people, city, etc. (just ideas!).

Logo is attached.

Requirement:
- Business Cards (2 Sided Full Color CMYK)
- Letterhead (1 Sided Full Color CMYK)
- Envelope (1 Sided Full Color CMYK)
- Sticker (1 Sided Full Color CMYK), round with a 2inch diameter.

Reason: We're starting to get more and more designs and need more time to look into all of them. Very exciting!! Thanks to everybody!

Hi all, we're in the process of selecting our favs. Though choices!!! Really good submissions. Will keep you posted and sorry for the delay.

Target Market(s)

Car drivers and owners between 21 and 45

Industry/Entity Type

Parking

Requirements
Must have
• Sticker should be round and include company URL nimbora.com and the new logo which we will attach soon.
Should not have
• Should not be too serious or boring.

```html
<!DOCTYPE html>
<html lang="en">
<head>
<meta charset="utf-8">
<title>Nimbora Business Card</title>
<link rel="stylesheet" href="https://fonts.googleapis.com/css2?family=Open+Sans:wght@400;700&display=swap">
<style>
  :root {
    --backdrop: #ecebe8;
    --card-white: #ffffff;
    --ink: #3a3a3a;
    --ink-soft: #4a4a4a;
    --rule: #9a9a9a;
    --brand-blue: #1f5fd6;
    --brand-blue-deep: #0c2f8f;
    --band-line-light: #5fb3e6;
    --band-line-dark: #2a2f5a;
    --band-dark: #2b2b2b;
    --band-mid: #555555;
    --back-light: #5a5a5a;
    --back-dark: #2f2f2f;
    --white: #ffffff;
  }
  * { margin: 0; padding: 0; box-sizing: border-box; }
  html, body {
    width: 1200px; height: 431px; overflow: hidden;
    background: var(--backdrop);
    font-family: "Open Sans", Arial, sans-serif;
  }
  .stage { position: relative; width: 1200px; height: 431px; }
  .card {
    position: absolute; top: 72px; width: 515px; height: 294px;
    overflow: hidden;
    box-shadow: 0 2px 6px rgba(0,0,0,0.25);
  }
  .card--front { left: 64px; background: var(--card-white); }
  .card--back {
    left: 625px;
    background: radial-gradient(ellipse at 50% 40%, var(--back-light) 0%, var(--back-dark) 85%);
  }

  /* front */
  .brand { position: absolute; left: 97px; top: 39px; display: flex; align-items: center; gap: 16px; }
  .brand__dot {
    width: 92px; height: 92px; border-radius: 50%;
    background: radial-gradient(circle at 40% 35%, var(--brand-blue) 0%, var(--brand-blue-deep) 100%);
  }
  .brand__name { font-size: 56px; font-weight: 400; color: var(--ink); letter-spacing: 1px; line-height: 1; }

  .address {
    position: absolute; right: 275px; top: 176px;
    text-align: right; font-size: 13px; line-height: 18px; color: var(--ink-soft);
  }
  .divider { position: absolute; left: 255px; top: 156px; width: 1px; height: 77px; background: var(--rule); }
  .contacts { position: absolute; left: 270px; top: 157px; list-style: none; }
  .contacts li {
    display: flex; align-items: center; gap: 7px;
    height: 19px; font-size: 13px; color: var(--ink-soft);
  }
  .contacts svg { width: 9px; height: 9px; fill: var(--ink); flex: none; }

  .band-line--light { position: absolute; left: 0; right: 0; top: 255px; height: 2px; background: var(--band-line-light); }
  .band-line--dark { position: absolute; left: 0; right: 0; top: 259px; height: 1px; background: var(--band-line-dark); }
  .name-band {
    position: absolute; left: 0; right: 0; top: 262px; height: 32px;
    background: linear-gradient(90deg, var(--band-dark) 0%, var(--band-mid) 50%, var(--band-dark) 100%);
    display: flex; align-items: center; justify-content: center;
    color: var(--white);
  }
  .name-band__name { font-size: 16px; font-weight: 700; }
  .name-band__title { font-size: 13px; font-weight: 400; margin-left: 4px; }

  /* back */
  .back-mark {
    position: absolute; left: 0; right: 0; top: 48px;
    display: flex; flex-direction: column; align-items: center; gap: 14px;
  }
  .back-mark__dot {
    width: 110px; height: 110px; border-radius: 50%;
    background: radial-gradient(circle at 40% 35%, var(--brand-blue) 0%, var(--brand-blue-deep) 100%);
  }
  .back-mark__name { font-size: 34px; font-weight: 400; color: var(--white); letter-spacing: 1px; line-height: 1; }
  .back-url {
    position: absolute; left: 0; right: 0; top: 245px;
    text-align: center; font-size: 18px; letter-spacing: 2px; color: var(--white);
  }
</style>
</head>
<body>
<main class="stage">
  <section class="card card--front">
    <div class="brand">
      <div class="brand__dot"></div>
      <span class="brand__name">nimbora</span>
    </div>

    <p class="address">Complex Name, Street Name<br>Area, City Name,000 000</p>
    <div class="divider"></div>
    <ul class="contacts">
      <li>
        <svg viewBox="0 0 10 10" aria-hidden="true"><path d="M2 0.5l2 2-1 1.2c.6 1.3 1.6 2.3 2.8 2.8L7 5.5l2.5 2-1 2C4.5 9.5.5 5.5.5 1.5z"/></svg>
        +91 12345 67890
      </li>
      <li>
        <svg viewBox="0 0 10 10" aria-hidden="true"><path d="M2.5 0h5v10h-5z M3.5 1.2v6h3v-6z"/></svg>
        +91 12345 67890
      </li>
      <li>
        <svg viewBox="0 0 10 10" aria-hidden="true"><path d="M0 2h10v7H0z M0.8 2.6L5 6l4.2-3.4v-.1H.8z" fill-rule="evenodd"/></svg>
        info@nimbora.com
      </li>
      <li>
        <svg viewBox="0 0 10 10" aria-hidden="true"><circle cx="5" cy="5" r="4.6"/></svg>
        www.nimbora.com
      </li>
    </ul>

    <div class="band-line--light"></div>
    <div class="band-line--dark"></div>
    <div class="name-band">
      <span class="name-band__name">Your Name ,</span><span class="name-band__title">Title</span>
    </div>
  </section>

  <section class="card card--back">
    <div class="back-mark">
      <div class="back-mark__dot"></div>
      <span class="back-mark__name">nimbora</span>
    </div>
    <p class="back-url">www.nimbora.com</p>
  </section>
</main>
</body>
</html>
```